Design a Website in Wordpress for an Australian Health Training Company in Health related courses

We require a WORDPRESS based Website (due to add on's we need to use for third party software) to replace our old site.
We offer national face to face delivery in medical reception, terminology and also administration.
The website will have around 6 pages and the ability to describe our main 6 courses (perhaps on the Courses page this may be tabs opening up to details for example?)
I have attached a previous sample of a Joomla site which was being developed (please do not feel you have to copy this - but I am just giving it as a sample - copying would be boring). But it gives an idea of look/feel and colours which may be suitable. Open to other ideas though.
I will provide some of the content, but would like the ability to finish the content myself.
Images and graphics are important. While a few medical photos re great - don't be tempted to us all pictures of doctors and nurses (although a couple would be good) - these are administrative courses so general corporate, eye catching visionary pictures of people in general are great. A medical type picture is also fine.
THE BOOKING system - will be via an ADD ON which will occur at the end of the project and is supplied by a third party software company (our student management system). This project will include up to 2 hours working with the Tech guys from the third party software to enable the ADD ON. If this ADD ON requires more time, we will pay hourly (although I do not expect it will).
Target Market(s)
Mostly a female market, many mature aged women target 25-45 yrs. Mixture of medical/health and corporate. Maybe a bit of mums returning to work and corporate inspiration.
Industry/Entity Type
It Company
Coding
Coded - Design and coding required
Number of Pages Required
5+ page
Requirements
Must have
- Wordpress
- Great graphics
- Interesting
- professional and clean
- Enquiry section (info Pak)
- Should have a University feel to it - Education
- Pages
- Home Page - About Us - Recruitment -Courses - Class Schedule - Traineeships Queensland Funding - Latest News Blog - Corporate Training- Contact us

```html
<!DOCTYPE html>
<html lang="en">
<head>
<meta charset="utf-8">
<title>Harbourline Institute of Training</title>
<link href="https://fonts.googleapis.com/css2?family=Lora:wght@700&family=Open+Sans:wght@400;600;700&display=swap" rel="stylesheet">
<style>
:root{
  --navy:#22335a;
  --navy-deep:#1c2b4d;
  --orange:#f7902e;
  --grey:#8b8b8b;
  --light:#efefef;
  --ink:#333a45;
  --footer:#2b2b2b;
  --white:#ffffff;
  --line:#d9dde3;
}
*{box-sizing:border-box;margin:0;padding:0}
html,body{width:1200px;height:2941px;overflow:hidden}
body{position:relative;font-family:"Open Sans",Arial,sans-serif;color:var(--ink);background:var(--white)}
.abs{position:absolute}
.top-rule{left:0;top:0;width:1200px;height:6px;background:var(--navy)}

/* header */
.brand{left:112px;top:20px;width:170px;text-align:center;font-family:"Lora",Georgia,serif;font-weight:700;color:var(--navy);font-size:15px;line-height:18px;text-transform:uppercase}
.brand-mark{display:block;width:58px;height:58px;margin:8px auto 0;background:var(--navy)}
.search{left:622px;top:25px;width:153px;height:42px;border:1px solid #cfd3d8;font-size:11px;color:#999;padding:13px 0 0 30px;letter-spacing:1px}
.search svg{position:absolute;left:12px;top:14px}
.btn-info{left:790px;top:25px;width:134px;height:42px;background:var(--orange);color:#fff;font-weight:700;font-size:14px;line-height:42px;padding-left:40px}
.btn-enrol{left:935px;top:25px;width:132px;height:42px;background:var(--navy);color:#fff;font-weight:700;font-size:14px;line-height:42px;padding-left:40px}
.btn-info svg,.btn-enrol svg{position:absolute;left:14px;top:12px}
.nav{left:331px;top:94px;display:flex;height:40px}
.nav a{display:flex;align-items:center;text-decoration:none;color:var(--ink);font-size:11.5px;line-height:14px;padding:0 10px;border-right:1px solid var(--line)}
.nav a:last-child{border-right:none}
.nav a.active{background:var(--navy);color:#fff;padding:0 16px}

/* hero */
.hero{left:0;top:153px;width:1200px;height:449px;background:
  radial-gradient(ellipse 160px 200px at 360px 200px,rgba(74,96,140,.55),transparent 70%),
  radial-gradient(ellipse 170px 210px at 640px 230px,rgba(210,218,230,.9),transparent 70%),
  radial-gradient(ellipse 150px 200px at 900px 260px,rgba(40,40,48,.45),transparent 70%),
  radial-gradient(ellipse 260px 120px at 140px 420px,rgba(230,232,236,.95),transparent 70%),
  radial-gradient(ellipse 300px 90px at 420px 430px,rgba(200,170,150,.45),transparent 70%),
  linear-gradient(100deg,#aebccb 0%,#e5e9ee 35%,#f4f5f7 55%,#cdd4dd 80%,#9fadbf 100%)}
.hero-arrow{width:52px;height:52px;border-radius:50%;background:var(--navy);top:352px}
.hero-arrow svg{position:absolute;left:18px;top:16px}
.hero-title{left:775px;top:422px;font-weight:700;color:#fff;font-size:47px;letter-spacing:.5px;text-shadow:0 2px 6px rgba(0,0,0,.35)}
.btn-orange{background:var(--orange);color:#fff;font-weight:700;text-transform:uppercase;text-align:center}
.hero-more{left:778px;top:494px;width:152px;height:41px;line-height:41px;font-size:15px}

/* courses */
.courses{left:0;top:602px;width:1200px;height:267px;background:var(--navy)}
.section-title{font-family:"Lora",Georgia,serif;font-weight:700;color:var(--orange);font-size:17px;letter-spacing:.5px}
.courses .section-title{position:absolute;left:0;width:1200px;top:36px;text-align:center}
.course{position:absolute;top:95px;width:200px;margin-left:-100px;text-align:center;color:#fff;font-weight:600;font-size:13px;line-height:19px}
.icon-round{width:67px;height:67px;border-radius:50%;background:var(--orange);display:flex;align-items:center;justify-content:center;margin:0 auto 26px;border:3px solid rgba(255,255,255,.25)}
.course-divider{position:absolute;top:95px;width:1px;height:120px;background:rgba(255,255,255,.18)}

/* welcome */
.welcome-kicker{left:133px;top:897px;font-size:14px;font-weight:700;color:var(--navy)}
.welcome-name{left:133px;top:920px;font-family:"Lora",Georgia,serif;font-weight:700;color:var(--navy);font-size:20px;line-height:22px;text-transform:uppercase;width:320px}
.welcome-text{left:133px;top:984px;width:560px;font-size:11.5px;line-height:19px;color:#444}
.welcome-text p{margin-bottom:13px}
.welcome-more{left:133px;top:1177px;width:118px;height:34px;line-height:34px;font-size:12px}
.crest-panel{left:735px;top:937px;width:340px;height:271px;border-left:1px solid #e3e3e3;text-align:center}
.crest-art{width:120px;height:120px;margin:40px auto 22px;background:var(--navy)}
.crest-name{font-family:"Lora",Georgia,serif;font-weight:700;font-size:15px;color:var(--navy)}

/* info + why */
.info-side{left:0;top:1241px;width:600px;height:577px;background:var(--grey)}
.why-side{left:600px;top:1241px;width:600px;height:577px;background:
  radial-gradient(ellipse 200px 260px at 180px 300px,rgba(70,92,138,.5),transparent 70%),
  radial-gradient(ellipse 180px 240px at 460px 220px,rgba(60,82,128,.45),transparent 70%),
  linear-gradient(135deg,#2a3d66,#22335a 60%,#1d2c4d)}
.info-title{left:133px;top:1281px;font-family:"Lora",Georgia,serif;font-weight:700;color:#fff;font-size:17px;letter-spacing:.5px}
.field{left:133px;width:387px;height:45px;background:#fff;font-size:12px;color:#333;padding:14px 0 0 30px}
.field svg{position:absolute;left:12px;top:15px}
.field .caret{left:auto;right:14px;top:18px}
.send{left:133px;top:1647px;width:387px;height:59px;line-height:59px;font-size:22px;letter-spacing:1px}
.why-title{left:647px;top:1281px}
.why-item{left:647px;width:430px;color:#fff}
.why-icon{position:absolute;left:0;top:0;width:55px;height:55px;border-radius:50%;background:var(--orange);display:flex;align-items:center;justify-content:center}
.why-item h3{margin-left:78px;font-size:12px;font-weight:700;letter-spacing:.3px;margin-bottom:6px}
.why-item p{margin-left:78px;font-size:10.5px;line-height:16px;color:#d8dde7}

/* blog */
.blog{left:0;top:1818px;width:1200px;height:470px;background:var(--light)}
.blog-title{left:133px;top:1858px}
.blog-arrows{left:1030px;top:1856px}
.card{top:1932px;width:222px;height:308px;background:#fff}
.card-img{position:absolute;left:8px;top:8px;width:206px;height:143px}
.img-clinic{background:
  radial-gradient(ellipse 50px 70px at 60px 80px,#f4f6f8,transparent 70%),
  radial-gradient(ellipse 50px 70px at 140px 70px,#e9eef3,transparent 70%),
  radial-gradient(ellipse 70px 30px at 110px 120px,#5fa6c9,transparent 70%),
  linear-gradient(135deg,#cfe0ec,#8fb4cf)}
.img-scan{background:
  radial-gradient(ellipse 55px 40px at 100px 70px,#7f8c99,transparent 70%),
  radial-gradient(ellipse 60px 30px at 150px 120px,#c9a58c,transparent 70%),
  linear-gradient(135deg,#3a3f4a,#12151b)}
.img-monitor{background:
  radial-gradient(ellipse 45px 20px at 80px 55px,rgba(70,200,120,.6),transparent 70%),
  radial-gradient(ellipse 45px 20px at 120px 90px,rgba(230,200,60,.5),transparent 70%),
  radial-gradient(ellipse 40px 18px at 90px 120px,rgba(60,150,230,.55),transparent 70%),
  linear-gradient(135deg,#27323f,#0f1820)}
.img-chart{background:
  radial-gradient(ellipse 60px 40px at 120px 80px,#2f6fb0,transparent 70%),
  radial-gradient(ellipse 80px 50px at 60px 60px,#f3f6fa,transparent 70%),
  linear-gradient(135deg,#e3ecf5,#7ea6cf)}
.date{position:absolute;left:83px;top:-30px;width:56px;height:56px;border-radius:50%;background:#fff;text-align:center;padding-top:8px;box-shadow:0 1px 3px rgba(0,0,0,.12)}
.date b{display:block;font-size:18px;color:var(--orange);line-height:20px}
.date span{font-size:8px;color:#555;text-transform:uppercase}
.card h4{position:absolute;left:16px;top:166px;width:196px;font-size:12px;line-height:17px;color:var(--navy);font-weight:700}
.card p{position:absolute;left:16px;top:204px;width:196px;font-size:10.5px;line-height:16px;color:#555;text-align:justify}
.card .more{position:absolute;left:16px;top:272px;font-size:10px;font-weight:700;color:var(--orange)}

/* testimonials */
.testimonials{left:0;top:2288px;width:1200px;height:334px;background:
  radial-gradient(ellipse 140px 180px at 170px 150px,rgba(90,110,150,.45),transparent 70%),
  radial-gradient(ellipse 140px 180px at 760px 120px,rgba(90,110,150,.4),transparent 70%),
  radial-gradient(ellipse 140px 180px at 1080px 200px,rgba(90,110,150,.45),transparent 70%),
  linear-gradient(90deg,#2b3e67,#34497a 50%,#2b3e67)}
.testi-title{left:0;width:1200px;top:2328px;text-align:center;color:#fff;font-family:"Lora",Georgia,serif;font-weight:700;font-size:17px}
.testi-rule{left:570px;top:2362px;width:60px;height:3px;background:var(--orange)}
.quote-mark{left:150px;top:2378px}
.testi-text{left:220px;top:2410px;width:760px;text-align:center;color:#fff;font-size:12.5px;line-height:24px}
.avatar{left:513px;top:2527px;width:48px;height:48px;border-radius:50%;background:linear-gradient(135deg,#f3d2b7,#c99a7d);border:2px solid #fff}
.person{left:577px;top:2533px;color:#fff}
.person b{display:block;font-size:12px}
.person span{font-size:10px;color:#d6dbe6}
.testi-arrow{top:2540px}

/* footer */
.footer{left:0;top:2622px;width:1200px;height:275px;background:var(--footer)}
.foot-brand{left:122px;top:2660px;width:180px;text-align:center;font-family:"Lora",Georgia,serif;font-weight:700;color:#fff;font-size:15px;line-height:18px;text-transform:uppercase}
.foot-brand .brand-mark{background:#fff;width:72px;height:72px;margin-top:14px}
.foot-divider{left:337px;top:2655px;width:1px;height:205px;background:#555}
.foot-head{color:#fff;font-size:12px;font-weight:700;letter-spacing:.3px}
.contact{left:363px;top:2700px;color:#fff;font-size:10.5px;line-height:15px}
.contact b{display:block;font-size:11px}
.contact div{margin-bottom:18px}
.foot-field{left:635px;width:212px;height:36px;background:#3c4e79;color:#fff;font-size:10px;padding:10px 0 0 12px}
.foot-msg{left:857px;top:2690px;width:212px;height:118px;background:#3c4e79;color:#fff;font-size:10px;padding:10px 0 0 12px}
.submit{left:982px;top:2830px;width:87px;height:33px;line-height:33px;font-size:11px}
.bottom-bar{left:0;top:2897px;width:1200px;height:44px;background:var(--orange)}
.follow{left:137px;top:2911px;font-size:10px;color:#222;display:flex;align-items:center;gap:8px}
.follow i{display:inline-block;width:22px;height:22px;border-radius:50%;background:var(--navy)}
.copy{left:890px;top:2913px;font-size:10px;color:#222}
</style>
</head>
<body>
<div class="abs top-rule"></div>

<!-- header -->
<div class="abs brand">Harbourline Institute<br>of Training<span class="brand-mark"></span></div>
<div class="abs search"><svg width="11" height="11" viewBox="0 0 11 11"><circle cx="4.5" cy="4.5" r="3.5" fill="none" stroke="#999" stroke-width="1.4"/><path d="M7 7l3 3" stroke="#999" stroke-width="1.4"/></svg>SEARCH</div>
<div class="abs btn-info"><svg width="18" height="18" viewBox="0 0 18 18"><circle cx="9" cy="9" r="8" fill="#fff"/><rect x="8" y="8" width="2" height="6" fill="#f7902e"/><circle cx="9" cy="5" r="1.2" fill="#f7902e"/></svg>INFO PACK</div>
<div class="abs btn-enrol"><svg width="16" height="18" viewBox="0 0 16 18"><path d="M5 17V6a1.5 1.5 0 013 0v5l5 1v5z" fill="#fff"/></svg>ENROL NOW</div>
<nav class="abs nav">
  <a class="active">Home</a><a>About Us</a><a>Recruitment</a><a>Courses</a><a>Class<br>Schedule</a><a>Traineeships<br>Queensland Funding</a><a>Latest<br>News Blog</a><a>Corporate<br>Training</a><a>Contact<br>us</a>
</nav>

<!-- hero -->
<div class="abs hero" role="img" aria-label="Photo of business professionals working together at laptops in a bright office"></div>
<div class="abs hero-arrow" style="left:37px"><svg width="14" height="20" viewBox="0 0 14 20"><path d="M10 3L3 10l7 7" fill="none" stroke="#fff" stroke-width="3"/></svg></div>
<div class="abs hero-arrow" style="left:1098px"><svg width="14" height="20" viewBox="0 0 14 20"><path d="M4 3l7 7-7 7" fill="none" stroke="#fff" stroke-width="3"/></svg></div>
<div class="abs hero-title">IT DIVISION</div>
<div class="abs btn-orange hero-more">Read More &raquo;</div>

<!-- courses -->
<section class="abs courses">
  <h2 class="section-title">OUR COURSES</h2>
  <div class="course" style="left:198px"><div class="icon-round"><svg width="30" height="30" viewBox="0 0 30 30"><rect x="3" y="7" width="24" height="18" rx="3" fill="none" stroke="#fff" stroke-width="2.4"/><path d="M15 11v10M10 16h10" stroke="#fff" stroke-width="2.6"/></svg></div>Medical Reception &amp;<br>Terminology</div>
  <div class="course-divider" style="left:296px"></div>
  <div class="course" style="left:406px"><div class="icon-round"><svg width="30" height="30" viewBox="0 0 30 30"><circle cx="15" cy="10" r="6" fill="#fff"/><path d="M4 28c0-7 5-11 11-11s11 4 11 11z" fill="#fff"/></svg></div>Cert III Business<br>Administration (Medical)</div>
  <div class="course-divider" style="left:510px"></div>
  <div class="course" style="left:592px"><div class="icon-round"><svg width="32" height="30" viewBox="0 0 32 30"><path d="M16 28L4 15a7 7 0 0112-9 7 7 0 0112 9z" fill="none" stroke="#fff" stroke-width="2.4"/><path d="M7 15h6l2-4 3 8 2-4h5" fill="none" stroke="#fff" stroke-width="2"/></svg></div>Medical<br>Terminology</div>
  <div class="course-divider" style="left:672px"></div>
  <div class="course" style="left:751px"><div class="icon-round"><svg width="32" height="24" viewBox="0 0 32 24"><rect x="2" y="3" width="28" height="18" rx="2" fill="none" stroke="#fff" stroke-width="2.2"/><path d="M7 9h2M12 9h2M17 9h2M22 9h2M7 13h2M12 13h2M17 13h2M22 13h2M10 17h12" stroke="#fff" stroke-width="2"/></svg></div>Keyboard<br>and Typing</div>
  <div class="course-divider" style="left:817px"></div>
  <div class="course" style="left:882px"><div class="icon-round"><svg width="30" height="30" viewBox="0 0 30 30"><circle cx="15" cy="15" r="12" fill="none" stroke="#fff" stroke-width="2.4"/><path d="M3 15h24M15 3c-6 7-6 17 0 24M15 3c6 7 6 17 0 24" fill="none" stroke="#fff" stroke-width="2"/></svg></div>Harbourline<br>Online</div>
  <div class="course-divider" style="left:950px"></div>
  <div class="course" style="left:1018px"><div class="icon-round"><svg width="26" height="30" viewBox="0 0 26 30"><path d="M7 13V9a6 6 0 0112 0v4" fill="none" stroke="#fff" stroke-width="2.6"/><rect x="3" y="13" width="20" height="15" rx="2" fill="#fff"/></svg></div><br>Confidentiality</div>
</section>

<!-- welcome -->
<div class="abs welcome-kicker">WELCOME TO</div>
<div class="abs welcome-name">Harbourline Institute<br>of Training</div>
<div class="abs welcome-text">
  <p>Harbourline is Australia's Leading Provider of Educational, Training and Support Services for the Medical and Dental industry - enabling students to be immediately skilled and 'Job Ready' for a career in Health.</p>
  <p>Harbourline is a Registered Training Organisation offering specialised Medical Administration Training in over 15 locations Australia wide. Harbourline have trained thousands of students the required knowledge and skills to become successful health care administrators.</p>
  <p>Our unique Short Medical Reception and Terminology Course and our Full Qualification is Nationally Accredited and the go-to recognised qualification in industry.</p>
</div>
<div class="abs btn-orange welcome-more">Read More &raquo;</div>
<div class="abs crest-panel">
  <div class="crest-art"></div>
  <div class="crest-name">Harbourline Institute of Training</div>
</div>

<!-- info pack + why -->
<div class="abs info-side"></div>
<div class="abs why-side" role="img" aria-label="Faint navy-toned background photo of students"></div>
<div class="abs info-title">EMAIL ME AN INFO PACK</div>
<div class="abs field" style="top:1330px"><svg width="11" height="12" viewBox="0 0 11 12"><circle cx="5.5" cy="3.5" r="3" fill="#333"/><path d="M0 12c0-4 2.5-6 5.5-6s5.5 2 5.5 6z" fill="#333"/></svg>Name</div>
<div class="abs field" style="top:1392px"><svg width="12" height="10" viewBox="0 0 12 10"><rect x=".7" y=".7" width="10.6" height="8.6" fill="none" stroke="#333" stroke-width="1.3"/><path d="M1 1l5 4 5-4" fill="none" stroke="#333" stroke-width="1.3"/></svg>E mail</div>
<div class="abs field" style="top:1455px"><svg width="12" height="12" viewBox="0 0 12 12"><rect x=".7" y="2" width="9" height="9" fill="none" stroke="#333" stroke-width="1.3"/><path d="M5 7l6-6" stroke="#333" stroke-width="1.5"/></svg>Course<svg class="caret" width="12" height="8" viewBox="0 0 12 8"><path d="M1 1l5 5 5-5" fill="none" stroke="#333" stroke-width="1.8"/></svg></div>
<div class="abs field" style="top:1518px"><svg width="12" height="12" viewBox="0 0 12 12"><circle cx="6" cy="6" r="5.5" fill="#333"/></svg>State</div>
<div class="abs field" style="top:1580px"><svg width="12" height="12" viewBox="0 0 12 12"><path d="M2 1l3 3-1.5 1.5a7 7 0 003 3L8 7l3 3-2 2C5 12 0 7 0 3z" fill="#333"/></svg>Mobile</div>
<div class="abs btn-orange send">SEND</div>

<div class="abs section-title why-title">WHY HARBOURLINE INSTITUTE ?</div>
<div class="abs why-item" style="top:1326px"><div class="why-icon"><svg width="26" height="26" viewBox="0 0 26 26"><path d="M5 12l5 5 11-11" fill="none" stroke="#fff" stroke-width="3.4"/></svg></div><h3>QUALITY</h3><p>Harbourline delivery quality, effective training facilitated by industry leaders. Just ask our students who rate us on average of 4.7 out of 5.</p></div>
<div class="abs why-item" style="top:1418px"><div class="why-icon"><svg width="28" height="28" viewBox="0 0 28 28"><circle cx="14" cy="14" r="9" fill="none" stroke="#fff" stroke-width="3" stroke-dasharray="4 3"/><circle cx="14" cy="14" r="4" fill="#fff"/></svg></div><h3>EXPERIENCE</h3><p>Harbourline is Australia's largest and leading providers of nationally recognised training in health administration – training from over 17 locations Australia wide.</p></div>
<div class="abs why-item" style="top:1516px"><div class="why-icon"><svg width="28" height="28" viewBox="0 0 28 28"><path d="M14 2l3.6 7.6 8.2 1-6 5.8 1.5 8.2L14 20.6l-7.3 4 1.5-8.2-6-5.8 8.2-1z" fill="#fff"/></svg></div><h3>VALUE</h3><p>Our innovative teaching approach allows us to deliver exceptional training at affordable prices with no hidden extras.</p></div>
<div class="abs why-item" style="top:1610px"><div class="why-icon"><svg width="28" height="26" viewBox="0 0 28 26"><path d="M2 24V12l7 4v-4l7 4V6h4v-4h4v22z" fill="#fff"/></svg></div><h3>INDUSTRY RECOGNISED</h3><p>Harbourline work hand in hand with industry to develop our core programme and consolidate the programme annually to keep the programme fresh and relevant.</p></div>
<div class="abs why-item" style="top:1710px"><div class="why-icon"><svg width="26" height="22" viewBox="0 0 26 22"><path d="M2 3h3M9 3h15M2 11h3M9 11h15M2 19h3M9 19h15" stroke="#fff" stroke-width="3"/></svg></div><h3>GREAT JOB RESULTS</h3><p>Harbourline students get jobs! Our focus is to create job-ready students who are mentored to achieve their goals. Harbourline also provide a recruitment service for industry and graduates.</p></div>

<!-- blog -->
<div class="abs blog"></div>
<div class="abs section-title blog-title">LATEST BLOG</div>
<div class="abs blog-arrows"><svg width="38" height="18" viewBox="0 0 38 18"><path d="M9 2L2 9l7 7M29 2l7 7-7 7" fill="none" stroke="#222" stroke-width="2.6"/></svg></div>

<article class="abs card" style="left:133px">
  <div class="card-img img-clinic" role="img" aria-label="Photo of a doctor and nurse reviewing a patient file"></div>
  <div class="date"><b>25</b><span>Jan</span></div>
  <h4>Short Course Medical Reception Training,</h4>
  <p>The Harbourline Medical Receptionist Training program is geared towards gaining employment and as part...</p>
  <span class="more">READ MORE</span>
</article>
<article class="abs card" style="left:371px">
  <div class="card-img img-scan" role="img" aria-label="Photo of a brain scan shown on a tablet held in hand"></div>
  <div class="date"><b>14</b><span>June</span></div>
  <h4>Contrary to popular belief, Lorem Ipsum is not.</h4>
  <p>The Harbourline Medical Receptionist Training program is geared towards gaining employment and as part...</p>
  <span class="more">READ MORE</span>
</article>
<article class="abs card" style="left:609px">
  <div class="card-img img-monitor" role="img" aria-label="Photo of a hospital patient monitor with vital signs"></div>
  <div class="date"><b>13</b><span>Feb</span></div>
  <h4>The standard chunk of Lorem Ipsum used since.</h4>
  <p>The Harbourline Medical Receptionist Training program is geared towards gaining employment and as part...</p>
  <span class="more">READ MORE</span>
</article>
<article class="abs card" style="left:847px">
  <div class="card-img img-chart" role="img" aria-label="Photo of a stethoscope resting on a medical chart"></div>
  <div class="date"><b>25</b><span>Jan</span></div>
  <h4>Lorem Ipsum is simply dummy text of the printinG.</h4>
  <p>The Harbourline Medical Receptionist Training program is geared towards gaining employment and as part...</p>
  <span class="more">READ MORE</span>
</article>

<!-- testimonials -->
<div class="abs testimonials" role="img" aria-label="Navy-tinted background photo of smiling office workers"></div>
<div class="abs testi-title">TESTIMONIALS</div>
<div class="abs testi-rule"></div>
<svg class="abs quote-mark" width="48" height="40" viewBox="0 0 48 40"><path d="M2 38V22C2 10 8 4 18 2l2 5c-6 2-9 6-9 11h9v20zM28 38V22C28 10 34 4 44 2l2 5c-6 2-9 6-9 11h9v20z" fill="rgba(255,255,255,.55)"/></svg>
<p class="abs testi-text">There are many variations of passages of Lorem Ipsum available, but the majority have suffered alteration in some form, by injected humour, or randomised words which don't look even slightly believable. If you are going to use a passage of Lorem Ipsum, you need to be sure there isn't anything embarrassing hidden in the middle of text. All the Lorem Ipsum generators on the Internet tend to repeat predefined chunks as necessary, making this the first true generator.</p>
<svg class="abs testi-arrow" style="left:468px" width="14" height="22" viewBox="0 0 14 22"><path d="M11 2L3 11l8 9" fill="none" stroke="#fff" stroke-width="3"/></svg>
<div class="abs avatar" role="img" aria-label="Student portrait"></div>
<div class="abs person"><b>DANIEL MORENO</b><span>Australia</span></div>
<svg class="abs testi-arrow" style="left:721px" width="14" height="22" viewBox="0 0 14 22"><path d="M3 2l8 9-8 9" fill="none" stroke="#fff" stroke-width="3"/></svg>

<!-- footer -->
<div class="abs footer"></div>
<div class="abs foot-brand">Harbourline Institute<br>of Training<span class="brand-mark"></span></div>
<div class="abs foot-divider"></div>
<div class="abs foot-head" style="left:363px;top:2661px">CONTACT US</div>
<div class="abs contact">
  <div><b>NEW SOUTH WALES, VICTORIA &amp; ACT</b>1800 555 014</div>
  <div><b>SOUTH AUSTRALIA, QUEENSLAND, NT</b>1800 555 027</div>
  <div><b>WESTERN AUSTRALIA</b>08 5550 1900</div>
</div>
<div class="abs foot-head" style="left:635px;top:2661px">ENQUIRY</div>
<div class="abs foot-field" style="top:2690px">Name</div>
<div class="abs foot-field" style="top:2733px">E mail</div>
<div class="abs foot-field" style="top:2776px">Phone</div>
<div class="abs foot-msg">Message</div>
<div class="abs btn-orange submit">SUBMIT</div>

<div class="abs bottom-bar"></div>
<div class="abs follow">Follow us on <i></i><i></i><i></i><i></i></div>
<div class="abs copy">Copyrights @ 2016 All Rights Reserved</div>
</body>
</html>
```